Outdoor Billboard on PVC (double sides)

Hello, i need special design for billboard which is located 15 meters away from the main road. Measures form Billboard: 8 meters X 2 meters. I need Billboard for Window tinting. I have one picture (white Varnelo) which you can use as a main BIG Picture- or you have better idea i am so open to your suggestions. Billboard has to be shocking ... i want to make it look like this is similiar way from style. I have a lot of pictures from my cars which i have done in my garage which we can use it. I dont know if you can use this ... quality? On the billboard so it blames be turn left in 30Meter. My logo wants bi attached- please use it on black background. text which schould be down on the Billboard: Proffesionale Tint my logo GLANTIX put somewhere where looks cool Phone: 0664 2915 087 E-mail: marlow.glantix@mailvento.com Website: www. glantix-scheibentoenung.at

Target Market(s)

This billboard wants to be on the border between two countrys..i have my garage company here on the border- where ia am making window. A lot of cars are driving each day nearby so I want that people see this and so they look at where they have left to my garage.

Colors

Designer to choose colors to be used in the design.

Requirements
Must have
• Billboard schould have a BiG picture from white Varnelo with my logo on the side and text Proffesional scarf tint. Down on the board it schould be info Tel, email, website. This measures 8x2 meters

```html
<!DOCTYPE html>
<html lang="de">
<head>
<meta charset="utf-8">
<title>GLANTIX – Professionelle Scheibentönung</title>
<link rel="stylesheet" href="https://fonts.googleapis.com/css2?family=Michroma&display=swap">
<style>
  :root {
    --page-bg: #e6e8eb;
    --board-black: #0b0b0c;
    --board-black-soft: #19191b;
    --brand-red: #e3161f;
    --brand-red-dark: #c8101a;
    --text-white: #ffffff;
    --silver-light: #e4e6e8;
    --silver-dark: #8c9095;
    --car-light: #d9dcdf;
    --car-mid: #8d9196;
    --car-dark: #2a2b2e;
  }
  * { margin: 0; padding: 0; box-sizing: border-box; }
  html, body {
    width: 1200px;
    height: 1000px;
    overflow: hidden;
    background: var(--page-bg);
  }
  .billboard {
    position: absolute;
    left: 57px;
    top: 359px;
    width: 1086px;
    height: 282px;
    transform: scale(1.0681);
    transform-origin: center;
    background: linear-gradient(180deg, var(--board-black-soft), var(--board-black) 60%);
    font-family: "Michroma", sans-serif;
    overflow: hidden;
  }
  .headline {
    position: absolute;
    left: 56px;
    top: 32px;
    width: 318px;
    text-align: center;
    line-height: 1;
  }
  .headline-top {
    display: block;
    color: var(--brand-red);
    font-size: 20px;
    letter-spacing: 2.6px;
  }
  .headline-bottom {
    display: block;
    margin-top: 6px;
    font-size: 20px;
    letter-spacing: 2.4px;
    background: linear-gradient(180deg, var(--silver-light) 30%, var(--silver-dark));
    -webkit-background-clip: text;
    background-clip: text;
    color: transparent;
  }
  .brand {
    position: absolute;
    left: 105px;
    top: 118px;
    width: 220px;
    text-align: center;
  }
  .brand-dot {
    display: block;
    width: 46px;
    height: 46px;
    margin: 0 auto 8px;
    border-radius: 50%;
    background: var(--brand-red);
  }
  .brand-name {
    display: block;
    color: var(--brand-red);
    font-size: 22px;
    letter-spacing: 1px;
    line-height: 1;
  }
  .phone {
    position: absolute;
    left: 75px;
    top: 210px;
    width: 280px;
    text-align: center;
    color: var(--text-white);
    font-size: 18px;
    letter-spacing: 2px;
    line-height: 1;
  }
  .car-photo {
    position: absolute;
    left: 393px;
    top: 37px;
    width: 652px;
    height: 210px;
    border-radius: 120px 160px 30px 30px;
    background: radial-gradient(ellipse at 50% 40%, var(--car-light) 0%, var(--car-mid) 60%, var(--car-dark) 100%);
  }
  .contact-band {
    position: absolute;
    left: 0;
    right: 0;
    bottom: 0;
    height: 37px;
    background: linear-gradient(180deg, var(--brand-red), var(--brand-red-dark));
    display: flex;
    align-items: center;
    justify-content: center;
    gap: 16px;
    color: var(--text-white);
    font-size: 13.5px;
    letter-spacing: 1.4px;
    text-transform: uppercase;
  }
  .contact-separator {
    width: 10px;
    height: 10px;
    background: var(--text-white);
  }
</style>
</head>
<body>
  <main class="billboard">
    <h1 class="headline">
      <span class="headline-top">PROFFESIONELLE</span>
      <span class="headline-bottom">SCHEIBENTÖNUNG</span>
    </h1>

    <div class="brand">
      <span class="brand-dot"></span>
      <span class="brand-name">GLANTIX</span>
    </div>

    <p class="phone">0664 2915 087</p>

    <div class="car-photo" role="img" aria-label="Photo of a white Varnelo sports coupé in side view with tinted windows"></div>

    <footer class="contact-band">
      <span class="contact-email">marlow.glantix@mailvento.com</span>
      <span class="contact-separator"></span>
      <span class="contact-web">www.glantix-scheibentoenung.at</span>
    </footer>
  </main>
</body>
</html>
```